Experienced and Professional Marriage Celebrant

I need a web design for my services as a marriage celebrant in the Sydney area. I want people to have the impression I am a modern and professional marriage celebrant who can tailor a wedding ceremony and execute the ceremony with a high level of care and accommodate and adapt to any style of wedding and personalities of couples. I like a mint and pink and black theme and I am not sure whether to use the professional photos of me, might be too stiff! But would like to see ideas you can come up with. Happy to use other photos you might have
Updates

Project Deadline Extended
Reason: I have haven't been able to respond as quickly as I would have liked this last week to comments so extending a few days. Thanks

Industry/Entity Type

It Professional

```html
<!DOCTYPE html>
<html lang="en">
<head>
<meta charset="utf-8">
<title>Mara Linden Celebrant – Services</title>
<link href="https://fonts.googleapis.com/css2?family=Roboto:wght@300;400;500&display=swap" rel="stylesheet">
<style>
:root{
  --black:#000;
  --nav:#444;
  --nav-line:#2e2e2e;
  --mint:#a4d63e;
  --pink:#f36fc0;
  --ink:#222;
  --body:#555;
  --footer:#333;
  --footer-text:#ddd;
  --white:#fff;
}
*{margin:0;padding:0;box-sizing:border-box}
html,body{width:1200px;height:1125px;overflow:hidden;background:var(--white)}
body{font-family:"Roboto",Arial,sans-serif;color:var(--body);position:relative}

.site-header{height:73px;background:var(--black);display:flex;align-items:center;justify-content:space-between;padding:0 74px}
.brand{font-weight:500;font-size:27px;letter-spacing:1.5px;color:var(--white);text-transform:uppercase}
.brand span{color:var(--pink)}
.header-contact{display:flex;align-items:center;gap:8px;font-size:17px;color:var(--mint);letter-spacing:.3px}
.header-contact strong{color:var(--white);font-weight:400}
.header-social{display:flex;gap:5px;margin-left:14px}
.header-social i{display:block;width:19px;height:19px;border-radius:50%;background:var(--pink)}

.main-nav{height:44px;background:var(--nav);border-bottom:2px solid var(--nav-line);display:flex;padding-left:74px}
.main-nav a{display:flex;align-items:center;height:42px;padding:0 19.5px;color:var(--white);font-size:14px;text-decoration:none;letter-spacing:.3px;margin-right:19px}
.main-nav a.active{background:var(--mint);color:var(--ink)}

.hero{height:200px;background:linear-gradient(90deg,#6d6f70 0%,#a39089 18%,#d9d6cc 38%,#f2ede6 48%,#e9b3ad 60%,#f1c0bd 75%,#c98f8b 90%,#8f8e8c 100%)}

.services{padding:42px 74px 0}
.services h1{font-weight:400;font-size:24px;color:var(--black);letter-spacing:.3px;margin-bottom:24px}
.services h1 span{color:var(--pink)}
.service-grid{display:grid;grid-template-columns:540px 540px;column-gap:0;row-gap:64px}
.service-grid .service:nth-child(n+3){margin-top:0}
.service{display:flex;gap:19px;height:138px}
.service-photo{width:207px;height:138px;flex:none}
.service h2{font-weight:400;font-size:16px;color:var(--ink);line-height:1;margin-top:1px;margin-bottom:5px;letter-spacing:.3px}
.service p{font-weight:300;font-size:13.6px;line-height:21.2px;width:290px;letter-spacing:.2px}
.row-3{margin-top:4px}

.photo-altar{background:linear-gradient(180deg,#efe9e2,#d9c9a6 55%,#6f8a4a)}
.photo-car{background:linear-gradient(180deg,#6aa8d8,#e8eaec 45%,#c74a55 60%,#d8d8d8)}
.photo-hall{background:linear-gradient(135deg,#3a5fb3,#c23d6b 50%,#e7a9c8)}
.photo-couple{background:linear-gradient(180deg,#9c9a92,#4d4a3a 55%,#8c5a45)}
.photo-estate{background:linear-gradient(180deg,#8fb6dd,#8a7e6d 45%,#f2f2f2 70%,#4e7a3a)}
.photo-pier{background:linear-gradient(180deg,#4a3526,#7fa8cc 35%,#2f5d86 55%,#8a8784)}

.site-footer{position:absolute;left:0;top:1023px;width:1200px;height:102px;background:var(--footer);display:flex;justify-content:space-between;align-items:center;padding:0 74px}
.copyright{font-weight:300;font-size:11.5px;line-height:20px;color:var(--footer-text)}
.connect{display:flex;align-items:center;gap:6px;font-size:11px;color:var(--white);letter-spacing:.3px}
.connect-label{margin-right:8px}
.connect i{display:block;width:30px;height:30px;border-radius:50%;background:var(--pink)}
.connect i.mint{background:var(--mint)}
</style>
</head>
<body>
<header class="site-header">
  <div class="brand">Mara Linden <span>Celebrant</span></div>
  <div class="header-contact">
    <svg width="15" height="15" viewBox="0 0 15 15" aria-hidden="true"><rect width="15" height="15" rx="2" fill="#a4d63e"/><path d="M4 3.5c.6-.5 1.3-.3 1.6.3l.6 1.2c.2.4.1.8-.2 1.1l-.4.4c.5 1 1.2 1.8 2.2 2.3l.4-.4c.3-.3.7-.4 1.1-.2l1.2.6c.6.3.8 1 .3 1.6-.8.9-2 1-3.2.3C5.9 9.8 4.5 8.3 3.7 6.6 3.2 5.4 3.3 4.2 4 3.5z" fill="#000"/></svg>
    <span>CALL US: <strong>123-456-7890</strong></span>
    <div class="header-social"><i></i><i></i><i></i></div>
  </div>
</header>

<nav class="main-nav">
  <a href="#">HOME</a>
  <a href="#">ABOUT US</a>
  <a href="#" class="active">SERVICES</a>
  <a href="#">NEWS &amp; EVENTS</a>
  <a href="#">GALLERY</a>
  <a href="#">TESTIMONIALS</a>
  <a href="#">BLOG</a>
  <a href="#">CONTACT US</a>
</nav>

<div class="hero" role="img" aria-label="Wedding couple dancing behind a champagne glass and a bouquet of pink roses"></div>

<main class="services">
  <h1>OUR <span>SERVICES</span></h1>
  <div class="service-grid">
    <article class="service">
      <div class="service-photo photo-altar" role="img" aria-label="Decorated wedding head table with gold chairs and white flowers"></div>
      <div><h2>Heading 1</h2><p>Aliquam molestie, mi et imperdiet euismod, dui purus auctor tellus, et interdum lacus lectus et ante. Aenean nonummy hendrerit mauris. Phasellus porta. Fusce suscipit varius mi. Cum sociis natoque penatibus et magnis dis parturient montes, nascetur ridiculus mus.</p></div>
    </article>
    <article class="service">
      <div class="service-photo photo-car" role="img" aria-label="White wedding car with a rose arrangement on the bonnet"></div>
      <div><h2>Heading 1</h2><p>Aliquam molestie, mi et imperdiet euismod, dui purus auctor tellus, et interdum lacus lectus et ante. Aenean nonummy hendrerit mauris. Phasellus porta. Fusce suscipit varius mi. Cum sociis natoque penatibus et magnis dis parturient montes, nascetur ridiculus mus.</p></div>
    </article>
    <article class="service">
      <div class="service-photo photo-hall" role="img" aria-label="Reception hall with colourful lighting and orchid centrepieces"></div>
      <div><h2>Heading 1</h2><p>Aliquam molestie, mi et imperdiet euismod, dui purus auctor tellus, et interdum lacus lectus et ante. Aenean nonummy hendrerit mauris. Phasellus porta. Fusce suscipit varius mi. Cum sociis natoque penatibus et magnis dis parturient montes, nascetur ridiculus mus.</p></div>
    </article>
    <article class="service">
      <div class="service-photo photo-couple" role="img" aria-label="Bride and groom laughing together by the water"></div>
      <div><h2>Heading 1</h2><p>Aliquam molestie, mi et imperdiet euismod, dui purus auctor tellus, et interdum lacus lectus et ante. Aenean nonummy hendrerit mauris. Phasellus porta. Fusce suscipit varius mi. Cum sociis natoque penatibus et magnis dis parturient montes, nascetur ridiculus mus.</p></div>
    </article>
    <article class="service row-3">
      <div class="service-photo photo-estate" role="img" aria-label="Garden venue with white chairs set before a large house"></div>
      <div><h2>Heading 1</h2><p>Aliquam molestie, mi et imperdiet euismod, dui purus auctor tellus, et interdum lacus lectus et ante. Aenean nonummy hendrerit mauris. Phasellus porta. Fusce suscipit varius mi. Cum sociis natoque penatibus et magnis dis parturient montes, nascetur ridiculus mus.</p></div>
    </article>
    <article class="service row-3">
      <div class="service-photo photo-pier" role="img" aria-label="Waterfront deck with chairs facing the sea"></div>
      <div><h2>Heading 1</h2><p>Aliquam molestie, mi et imperdiet euismod, dui purus auctor tellus, et interdum lacus lectus et ante. Aenean nonummy hendrerit mauris. Phasellus porta. Fusce suscipit varius mi. Cum sociis natoque penatibus et magnis dis parturient montes, nascetur ridiculus mus.</p></div>
    </article>
  </div>
</main>

<footer class="site-footer">
  <div class="copyright">Copyright © 2014. Mara Linden Celebrant.<br>All Right Reserved</div>
  <div class="connect"><span class="connect-label">CONNECT US:</span><i class="mint"></i><i></i><i class="mint"></i></div>
</footer>
</body>
</html>
```